Fresh Dwelling Tract Guide needs a new Landing Page

I like to get a landing page or website with 2-3 pages to help target home buyers who are looking to buy homes from builders such as TW Residences, Morvik, P.L. Fennick, etc. The landing page/website to be non-cluttered and be able to explain to home buyers that there are many benefits to include me as their buyer's agent when they buy a brand new home from any builders.
I may want to incorporate a short explanation video (animated) on the landing page and then for the viewer to click on a button that will take them to another page where they can search for new homes from different builders.
Target Market(s)
Home buyers looking to buy brand new home from builders such as TW Residences, Morvik, P.L. Fennick, etc.
Industry/Entity Type
Real Estate
Number of Pages Required
2 page
Font styles to use
Requirements
Must have
- The landing page may have the explanation video at the bottom of the landing page (scrolled down) or there may be a CALL TO ACTION button that takes the viewer to the 2nd page to watch the explanation video. Once they watched the explanation video and are still interested, they can click on another CALL TO ACTION button that will take them to another website that they will be able to search for all the available new homes and register their contact information.
Should not have
- No clutters and no dark colors.

```html
<!DOCTYPE html>
<html lang="en">
<head>
<meta charset="utf-8">
<title>Fresh Dwelling Tract Guide — Landing Page</title>
<link rel="stylesheet" href="https://fonts.googleapis.com/css2?family=Open+Sans:wght@400;600;700;800&family=Libre+Baskerville&display=swap">
<style>
  :root {
    --page-bg: #ffffff;
    --hero-purple: #6a22a6;
    --hero-purple-light: #7d35b5;
    --hero-purple-deep: #5a1f93;
    --button-dark: #3f1563;
    --text-light: #ffffff;
    --nav-underline: #ffffff;
  }
  * { box-sizing: border-box; margin: 0; padding: 0; }
  html, body {
    width: 1200px; height: 1200px; overflow: hidden;
    background: var(--page-bg);
  }
  .canvas {
    position: relative; width: 1200px; height: 1200px;
    display: flex; align-items: center;
  }
  .hero {
    position: relative; width: 1200px; height: 691px;
    color: var(--text-light);
    font-family: "Open Sans", Arial, sans-serif;
    overflow: hidden;
  }
  .hero-photo {
    position: absolute; inset: 0;
    background: linear-gradient(120deg, var(--hero-purple-deep) 0%, var(--hero-purple-light) 45%, var(--hero-purple) 75%, var(--hero-purple-deep) 100%);
  }
  .brand {
    position: absolute; left: 34px; top: 34px;
    font-size: 44px; font-weight: 600; letter-spacing: -0.5px; line-height: 1;
  }
  .main-nav {
    position: absolute; left: 225px; top: 58px;
    display: flex; gap: 31px; font-size: 11.5px;
  }
  .main-nav a { color: var(--text-light); text-decoration: none; position: relative; }
  .main-nav a.is-active::after {
    content: ""; position: absolute; left: 0; right: 0; bottom: -9px;
    height: 2px; background: var(--nav-underline);
  }
  .btn {
    position: absolute; display: flex; align-items: center; justify-content: center;
    font-size: 12px; font-weight: 700; letter-spacing: 1.6px; text-transform: uppercase;
    color: var(--text-light); text-decoration: none;
  }
  .btn-solid { background: var(--button-dark); box-shadow: 0 4px 14px rgba(40,10,70,0.35); }
  .btn-contact { left: 946px; top: 38px; width: 187px; height: 56px; font-size: 12.5px; }
  .hero-title {
    position: absolute; left: 0; right: 0; top: 215px; text-align: center;
    font-size: 78px; font-weight: 700; line-height: 101px; letter-spacing: 0.5px;
    text-shadow: 0 4px 12px rgba(40,10,70,0.3);
  }
  .hero-lede {
    position: absolute; left: 0; right: 0; top: 420px; text-align: center;
    font-family: "Libre Baskerville", Georgia, serif; font-size: 16.5px; line-height: 22px;
  }
  .btn-outline {
    left: 396px; top: 510px; width: 186px; height: 55px;
    border: 1.5px solid var(--text-light); gap: 28px; padding-left: 6px;
  }
  .btn-start { left: 609px; top: 510px; width: 187px; height: 55px; }
</style>
</head>
<body>
<main class="canvas">
  <section class="hero">
    <div class="hero-photo" role="img" aria-label="Aerial photo of terraced modern townhouses with rooftop gardens, tinted purple"></div>
    <div class="brand">logo</div>
    <nav class="main-nav">
      <a href="#" class="is-active">Home</a>
      <a href="#">How We Help</a>
      <a href="#">Who We Help</a>
      <a href="#">Client Successes</a>
      <a href="#">Technology</a>
      <a href="#">Resources</a>
      <a href="#">Company</a>
    </nav>
    <a href="#" class="btn btn-solid btn-contact">Contact Us</a>
    <h1 class="hero-title">NEIGHBORS BUILDING<br>NEIGHBORHOODS</h1>
    <p class="hero-lede">Lorem ipsum dolor sit amet, consectetur adipisicing elit, sed do eiusmod<br>tempor incididunt ut labore et dolore magna aliqua.</p>
    <a href="#" class="btn btn-outline">Play Video
      <svg width="24" height="24" viewBox="0 0 24 24" aria-hidden="true">
        <circle cx="12" cy="12" r="10.5" fill="none" stroke="#fff" stroke-width="2"/>
        <path d="M9.5 7.5 L16.5 12 L9.5 16.5 Z" fill="#fff"/>
      </svg>
    </a>
    <a href="#" class="btn btn-solid btn-start">Get Started</a>
  </section>
</main>
</body>
</html>
```